International IT business needs website revamp.

Velmor Limited would like their current website (www.velmorlimited-example.com) to be revamped/modernized to reflect up-to-date goods and services. Currently, Velmor is offering a conversational AI workflow platform for both enterprise clients and as a DIY solution for SMBs. This platform is called tqFlowbin and allows organizations to automate simple and repetitive workflows to drive their operational efficiency. In addition to the solution offering, Velmor Limited also provides professional IT services. With that said, please use www.velmorlimited-example.com and www.tqflowbin-example.ai for reference of current logos and colourways desired. Furthermore, refer to the attached PDF for a general idea of what to include in the site. The final design should be easy to navigate, clear, concise, and emphasize tqFlowbin as a solution for enterprise clients (while redirecting SMBs to the tqFlowbin website) looking to automate workflow processes/kickstart their digital transformation journey.

```html
<!DOCTYPE html>
<html lang="en">
<head>
<meta charset="utf-8">
<title>Velmor Limited</title>
<link href="https://fonts.googleapis.com/css2?family=Poppins:wght@300;400;500;600&family=Roboto:wght@400;500;700&display=swap" rel="stylesheet">
<style>
:root{
  --blue:#1b8dcf;
  --teal:#3db3a6;
  --ink:#222;
  --text:#6d6d6d;
  --light:#f6f6f6;
  --line:#e3e3e3;
  --white:#fff;
}
*{box-sizing:border-box;margin:0;padding:0}
html,body{width:1200px;height:4084px;overflow:hidden}
body{position:relative;background:var(--white);font-family:'Poppins',sans-serif;color:var(--text)}
.abs{position:absolute}
.h2{font-family:'Roboto',sans-serif;font-weight:500;color:var(--ink);font-size:40px;text-align:center;left:0;right:0}
.underline{height:4px;width:62px;background:var(--blue);margin:12px auto 0}

/* top bar */
.topbar{top:0;left:0;width:1200px;height:44px;font-size:14px;color:#333}
.topbar .item{top:12px;display:flex;align-items:center;gap:10px}
.ico{width:26px;height:26px;border:1.5px solid #333;border-radius:50%;display:flex;align-items:center;justify-content:center}
.social{top:9px;left:990px;display:flex;gap:6px}
.social span{width:26px;height:26px;border:1.5px solid #333;border-radius:50%}

/* nav */
.nav{top:44px;left:0;width:1200px;height:72px;background:var(--blue);color:var(--white)}
.brand{display:flex;align-items:center;gap:8px;font-family:'Poppins',sans-serif;font-weight:400;font-size:30px;color:var(--white);letter-spacing:1px}
.brand .mark{width:40px;height:40px;border:3px solid var(--white)}
.nav .brand{top:16px;left:111px}
.menu{top:27px;left:421px;display:flex;gap:0;font-size:14px}
.menu a{color:var(--white);text-decoration:none;position:absolute;white-space:nowrap}
.menu a.active{border-bottom:1.5px solid var(--white);padding-bottom:3px}
.login{top:16px;left:969px;width:122px;height:38px;background:#4cb7e2;border:2px solid #7fd0ee;color:var(--white);font-size:14px;display:flex;align-items:center;justify-content:center}

/* hero */
.hero-band{top:116px;left:0;width:1200px;height:824px;background:var(--light)}
.hero-photo{top:116px;left:0;width:1200px;height:680px;background:linear-gradient(135deg,#b9c4cc 0%,#e2e6ea 35%,#f1f2f3 55%,#8d98a6 80%,#4f5b6a 100%)}
.hero-curve{top:620px;left:0}
.hero-card{top:284px;left:306px;width:593px;height:295px;background:rgba(240,242,245,.88);text-align:center}
.product{display:inline-flex;align-items:center;gap:12px;margin-top:26px;font-size:50px;color:#29a6e0;font-weight:400}
.product .dot{width:54px;height:54px;border-radius:50%;background:#29a6e0}
.hero-card p{font-size:15px;color:#333;line-height:34px;margin-top:10px}
.btn{display:inline-flex;align-items:center;justify-content:center;background:var(--blue);color:var(--white);font-size:14px;font-weight:500}
.hero-card .btn{width:155px;height:50px;margin-top:10px}
.chev{top:395px}
.partners{top:838px;left:0;width:1200px;height:60px}
.partners span{position:absolute;top:18px;font-family:'Poppins',sans-serif;font-weight:500;font-size:17px;color:#333;display:flex;align-items:center;gap:8px;white-space:nowrap}
.partners i{display:inline-block;width:18px;height:18px;background:#c8c8c8}

/* about */
.about-title{top:1098px;left:111px;font-family:'Roboto',sans-serif;font-weight:500;font-size:40px;color:var(--ink)}
.about-line{top:1159px;left:111px;width:60px;height:4px;background:var(--blue)}
.about-text{top:1190px;left:111px;width:480px;font-size:15px;line-height:34.5px;text-align:justify;color:var(--text)}
.about .btn{top:1418px;left:111px;width:155px;height:50px}
.about-ring{top:1038px;left:609px;width:482px;height:486px;border-radius:50%;border:6px solid var(--teal)}
.about-photo{top:1048px;left:613px;width:474px;height:474px;border-radius:50%;background:linear-gradient(135deg,#cfd6dd,#6f7e8f 60%,#2f3b4b);border:5px solid var(--white)}

/* services */
.services{top:1628px;left:0;width:1200px;height:666px;background:#f3f3f3}
.services .h2{top:1684px}
.services .underline{position:absolute;top:1740px;left:569px;margin:0}
.card{background:var(--white);border:1px solid var(--line);box-shadow:0 1px 4px rgba(0,0,0,.08)}
.svc{top:1775px;width:318px;height:452px}
.svc .img{position:absolute;top:5px;left:5px;right:5px;height:249px}
.svc h3{position:absolute;top:278px;left:14px;font-size:14px;font-weight:600;color:#333}
.svc p{position:absolute;top:306px;left:14px;right:14px;font-size:12.3px;line-height:25.5px;text-align:justify;color:var(--text)}
.arrow-btn{top:2001px;width:42px;height:42px;border:1.5px solid #555;border-radius:50%;background:var(--white);display:flex;align-items:center;justify-content:center}

/* reviews */
.reviews-bg{top:2346px;left:0;width:1200px;height:370px;background:linear-gradient(90deg,#eef1f3,#fafbfc 40%,#f6f7f9)}
.reviews .h2{top:2386px}
.review{top:2458px;width:320px;height:190px;padding:22px 20px}
.review p{font-size:12px;line-height:22.5px;text-align:justify;color:var(--text)}
.review .who{display:flex;align-items:center;gap:10px;margin-top:10px;font-size:12px;font-weight:500;color:#333}
.review .who i{width:32px;height:2px;background:var(--blue)}
.review .stars{margin:6px 0 0 40px;color:var(--blue);font-size:11px;letter-spacing:3px}
.review .quote{position:absolute;right:4px;bottom:-14px;font-family:'Roboto',sans-serif;font-size:110px;color:#dde6ee;line-height:1}
.dots{top:2679px;left:558px;display:flex;gap:8px}
.dots span{width:14px;height:14px;border:1.5px solid #777;border-radius:50%}
.dots span.on{background:var(--teal);border-color:var(--teal)}

/* video */
.promo .h2{top:2788px}
.video{top:2869px;left:111px;width:978px;height:512px;background:linear-gradient(120deg,#4a3a2e,#d8dde2 35%,#eef0f2 55%,#7a6a5c 80%,#2a2520)}
.video .brand{position:absolute;top:40px;left:38px}
.video .caption{position:absolute;left:27px;bottom:38px;font-family:'Roboto',sans-serif;font-weight:500;font-size:23px;color:var(--white);letter-spacing:.5px}
.video .play{position:absolute;top:226px;left:458px;width:62px;height:44px;border-radius:10px;background:rgba(0,0,0,.55);display:flex;align-items:center;justify-content:center}

/* clients */
.clients{top:3500px;left:0;width:1200px;height:268px;background:var(--light)}
.clients .h2{top:3553px}
.clients span{position:absolute;top:3650px;font-family:'Poppins',sans-serif;font-weight:600;font-size:44px;color:#1f4f9a}

/* footer */
.footer{top:3768px;left:0;width:1200px;height:316px;background:var(--blue);color:var(--white);font-size:14px}
.footer .brand{position:absolute;top:42px;left:111px}
.fmenu a{position:absolute;top:70px;color:var(--white);text-decoration:none}
.contact{position:absolute;top:140px;display:flex;gap:18px}
.contact .ring{width:56px;height:56px;border:1.5px solid rgba(255,255,255,.7);border-radius:50%;display:flex;align-items:center;justify-content:center;flex:none}
.contact b{display:block;font-weight:500;font-size:14px;margin-top:8px}
.contact span{display:block;line-height:23px}
.fbottom{position:absolute;top:275px;font-size:15px}
</style>
</head>
<body>

<!-- top bar -->
<div class="abs topbar">
  <div class="abs item" style="left:111px">
    <span class="ico"><svg width="14" height="14" viewBox="0 0 24 24"><path d="M6.6 10.8a15 15 0 0 0 6.6 6.6l2.2-2.2c.3-.3.7-.4 1-.2 1.1.4 2.3.6 3.6.6.6 0 1 .4 1 1V20c0 .6-.4 1-1 1A17 17 0 0 1 3 4c0-.6.4-1 1-1h3.5c.6 0 1 .4 1 1 0 1.3.2 2.5.6 3.6.1.3 0 .7-.2 1z" fill="none" stroke="#333" stroke-width="1.8"/></svg></span>
    <span style="font-weight:500">CALL US - 1 (555) 014-2290</span>
  </div>
  <div class="abs item" style="left:510px">
    <span class="ico"><svg width="14" height="11" viewBox="0 0 24 18"><rect x="1" y="1" width="22" height="16" fill="none" stroke="#333" stroke-width="2"/><path d="M1 1l11 9 11-9" fill="none" stroke="#333" stroke-width="2"/></svg></span>
    <span>Email us : INFO@VELMORLIMITED-EXAMPLE.COM</span>
  </div>
  <div class="abs social" aria-label="Social links"><span></span><span></span><span></span></div>
</div>

<!-- navigation -->
<div class="abs nav">
  <div class="abs brand"><span class="mark"></span>VELMOR</div>
  <nav class="abs menu">
    <a class="active" style="left:0">HOME</a>
    <a style="left:80px">ABOUT</a>
    <a style="left:200px">SERVICES</a>
    <a style="left:305px">PRODUCTS</a>
    <a style="left:420px">CONTACT</a>
  </nav>
  <div class="abs login">LOG IN</div>
</div>

<!-- hero -->
<div class="abs hero-band"></div>
<div class="abs hero-photo" role="img" aria-label="Presenter in glasses speaking to a team around a meeting table"></div>
<svg class="abs hero-curve" width="1200" height="180" viewBox="0 0 1200 180">
  <path d="M0 50 Q600 220 1200 50 L1200 180 L0 180Z" fill="#f6f6f6"/>
  <path d="M160 105 Q600 200 1070 92" fill="none" stroke="#3db3a6" stroke-width="5"/>
</svg>
<div class="abs hero-card">
  <div class="product"><span class="dot"></span>tqFlowbin</div>
  <p>Velmor offers a complete turnkey solution for enterprise<br>customers to assist in their digital</p>
  <span class="btn">GET STARTED</span>
</div>
<svg class="abs chev" style="left:72px" width="16" height="28" viewBox="0 0 16 28"><path d="M14 2L2 14l12 12" fill="none" stroke="#fff" stroke-width="2"/></svg>
<svg class="abs chev" style="left:1100px" width="16" height="28" viewBox="0 0 16 28"><path d="M2 2l12 12L2 26" fill="none" stroke="#fff" stroke-width="2"/></svg>

<div class="abs partners">
  <span style="left:111px"><i></i>Northfield Services</span>
  <span style="left:318px"><i></i>Harbourline Registry</span>
  <span style="left:640px"><i></i>Lakeshore Realty Board</span>
  <span style="left:950px"><i></i>Routewise Club</span>
</div>

<!-- about -->
<section class="about">
  <h2 class="abs about-title">ABOUT US</h2>
  <div class="abs about-line"></div>
  <p class="abs about-text">The Velmor team is built with trusted IT professionals and in the past has delivered a broad spectrum of projects for major Canadian telecommunication and financial companies. Our staff are highly experienced in technology integration, legacy modernization, system architecture design, application development, quality assurance, and project management.</p>
  <span class="abs btn">READ MORE</span>
  <div class="abs about-ring"></div>
  <div class="abs about-photo" role="img" aria-label="Two colleagues reviewing documents at a laptop"></div>
</section>

<!-- services -->
<div class="abs services"></div>
<section class="services-content">
  <h2 class="abs h2" style="top:1684px">OUR SERVICES</h2>
  <div class="abs" style="top:1744px;left:569px;width:62px;height:4px;background:var(--blue)"></div>
  <div class="abs arrow-btn" style="left:61px"><svg width="10" height="16" viewBox="0 0 10 16"><path d="M9 1L2 8l7 7" fill="none" stroke="#555" stroke-width="1.5"/></svg></div>
  <div class="abs arrow-btn" style="left:1091px"><svg width="10" height="16" viewBox="0 0 10 16"><path d="M1 1l7 7-7 7" fill="none" stroke="#555" stroke-width="1.5"/></svg></div>
  <article class="abs card svc" style="left:111px">
    <div class="img" role="img" aria-label="Engineers working in a server room" style="background:linear-gradient(135deg,#2a5a8a,#7fa6c8 50%,#1d3550)"></div>
    <h3>RESEARCH</h3>
    <p>Velmor is a competitive player in the IT sector. We will research and apply the latest cutting-edge technologies in software development to solve your IT issues in the most cost-effective way.</p>
  </article>
  <article class="abs card svc" style="left:439px">
    <div class="img" role="img" aria-label="Business team discussing a chart on a flipboard" style="background:linear-gradient(135deg,#5c4a3a,#d9d6cf 45%,#f0eee9 65%,#8a7968)"></div>
    <h3>ANALYSIS</h3>
    <p>We will complete a thorough feasibility study to identify and understand exactly what you require from the project and its overall viability. Afterwards, we provide a thourough briefing on project feasability.</p>
  </article>
  <article class="abs card svc" style="left:767px">
    <div class="img" role="img" aria-label="Smiling colleagues gathered around a laptop" style="background:linear-gradient(135deg,#3c4450,#cfd3d8 45%,#e8e9eb 60%,#444c57)"></div>
    <h3>DESIGN</h3>
    <p>Work with us every step of the way as we perform a prototype architecture design to develop an application that will target and fulfill each of the requirements that were demanded from your project proposal.</p>
  </article>
</section>

<!-- reviews -->
<div class="abs reviews-bg" role="img" aria-label="Faded office team background"></div>
<section class="reviews">
  <h2 class="abs h2" style="top:2386px">CUSTOMER REVIEWS</h2>
  <article class="abs card review" style="left:111px">
    <p>Naturally, the Northfield Passports website receives thousands of visitors a day. As a result, we noticed the need to automate simple and repetitive questions to provide quick, on-demand</p>
    <div class="who"><i></i>NORTHFIELD PASSPORTS</div>
    <div class="stars">★★★★★</div>
    <span class="quote">”</span>
  </article>
  <article class="abs card review" style="left:440px">
    <p>Leveraging tqFlowbin's extremely user-friendly interface, Northfield Services was able to implement our own bot for the My Northfield Account (MNA) page without the assistance of Velmor developers.</p>
    <div class="who"><i></i>NORTHFIELD SERVICES</div>
    <div class="stars">★★★★★</div>
    <span class="quote">”</span>
  </article>
  <article class="abs card review" style="left:769px">
    <p>Our company, Tallspire Builds, was able to deploy our salesbot instance within one month! We were extremely satisfied with tqFlowbin, we are discussing the introduction of a new capability to our bot.</p>
    <div class="who"><i></i>TALLSPIRE BUILDS</div>
    <div class="stars">★★★★★</div>
    <span class="quote">”</span>
  </article>
  <div class="abs dots"><span></span><span></span><span class="on"></span><span></span></div>
</section>

<!-- promotional video -->
<section class="promo">
  <h2 class="abs h2" style="top:2788px">PROMOTIONAL VIDEOS</h2>
  <div class="abs video" role="img" aria-label="Video still of a presenter at a whiteboard with a seated team">
    <div class="brand"><span class="mark"></span>VELMOR</div>
    <div class="play"><svg width="18" height="20" viewBox="0 0 18 20"><path d="M2 2l14 8-14 8z" fill="#fff"/></svg></div>
    <div class="caption">A CORE TEAM THAT HAS WORKED TOGETHER</div>
  </div>
</section>

<!-- clients -->
<section class="abs clients"></section>
<h2 class="abs h2" style="top:3553px">OUR CLIENTS</h2>
<div class="clients-row">
  <span class="abs" style="top:3650px;left:111px;font-weight:600;font-size:42px;color:#1f4f9a">Corvane</span>
  <span class="abs" style="top:3658px;left:368px;font-weight:600;font-size:34px;color:#5b5f74">Paylume</span>
  <span class="abs" style="top:3650px;left:656px;font-weight:600;font-size:42px;color:#222">Brightbay</span>
  <span class="abs" style="top:3650px;left:940px;font-weight:600;font-size:42px;color:#1f4f9a">Routewise</span>
</div>

<!-- footer -->
<footer class="abs footer">
  <div class="brand"><span class="mark"></span>VELMOR</div>
  <nav class="fmenu">
    <a style="left:400px">HOME</a>
    <a style="left:509px">ABOUT</a>
    <a style="left:624px">SERVICES</a>
    <a style="left:758px">PRODUCTS</a>
    <a style="left:904px">CONTACT</a>
  </nav>
  <div class="contact" style="left:111px">
    <div class="ring"><svg width="22" height="22" viewBox="0 0 24 24"><path d="M6.6 10.8a15 15 0 0 0 6.6 6.6l2.2-2.2c.3-.3.7-.4 1-.2 1.1.4 2.3.6 3.6.6.6 0 1 .4 1 1V20c0 .6-.4 1-1 1A17 17 0 0 1 3 4c0-.6.4-1 1-1h3.5c.6 0 1 .4 1 1 0 1.3.2 2.5.6 3.6.1.3 0 .7-.2 1z" fill="none" stroke="#fff" stroke-width="1.5"/></svg></div>
    <div><b>PHONE</b><span>+1 (555) 014-2290</span></div>
  </div>
  <div class="contact" style="left:453px">
    <div class="ring"><svg width="16" height="22" viewBox="0 0 16 22"><path d="M8 21s7-8 7-13A7 7 0 0 0 1 8c0 5 7 13 7 13z" fill="#fff"/><circle cx="8" cy="8" r="2.6" fill="#1b8dcf"/></svg></div>
    <div><b>ADDRESS</b><span>Velmor Ltd. 412 Ashgrove Road,<br>Unit 7 &amp; 8 Brackenton, ON<br>Canada K0X 9Z9</span></div>
  </div>
  <div class="contact" style="left:852px;top:132px">
    <div class="ring" style="margin-top:8px"><svg width="22" height="16" viewBox="0 0 24 18"><rect x="1" y="1" width="22" height="16" fill="none" stroke="#fff" stroke-width="1.5"/><path d="M1 1l11 9 11-9" fill="none" stroke="#fff" stroke-width="1.5"/></svg></div>
    <div><b>EMAIL</b><span>Info@velmorlimited-example.com</span></div>
  </div>
  <div class="fbottom" style="left:111px">Terms&amp;Conditions</div>
  <div class="fbottom" style="left:505px">© 2020 All Rights Reserved</div>
  <div class="fbottom" style="left:990px">Privacy Policy</div>
</footer>

</body>
</html>
```